The book is called "Distance Racing Blueprints: An In-Depth Manual for Achieving Your Peak Race Day - Featuring Schedules, Counsel and Target-Reaching Pointers "

It is a 6" x 9" book with 205 pages. This is an advanced book for runners who have been running and trying to hit their marathon goals, but haven't been able to do so. This needs to portray a professional coaching image and high performing athlete.

I have running photos of myself running marathons if you thought that was the route to take, but I'm open to your creative influence.

```html
<!DOCTYPE html>
<html lang="en">
<head>
<meta charset="utf-8">
<title>Distance Racing Blueprints – Cover Spread</title>
<link rel="stylesheet" href="https://fonts.googleapis.com/css2?family=Bebas+Neue&family=Oswald:wght@500;700&family=Roboto:ital,wght@0,700;1,300&family=Arimo&display=swap">
<style>
  :root{
    --stage:#2a2a2a;
    --paper:#f7f7f7;
    --red-dark:#a50d10;
    --red:#e3141a;
    --ink:#1d1d1d;
    --ink-soft:#2b2b2b;
    --photo-a:#e9e3de;
    --photo-b:#c7b9b0;
  }
  *{margin:0;padding:0;box-sizing:border-box}
  html,body{width:1200px;height:1200px;overflow:hidden;background:var(--stage)}
  .spread{position:absolute;left:40px;top:204px;width:1120px;height:792px;background:var(--paper)}

  .red-gradient{
    background:linear-gradient(180deg,var(--red-dark) 0%,var(--red) 55%,var(--red-dark) 100%);
    -webkit-background-clip:text;background-clip:text;color:transparent;
  }

  /* Back cover */
  .back{position:absolute;left:49px;top:44px;width:430px}
  .back-title{font-family:"Oswald",sans-serif;font-weight:700;font-size:33px;line-height:44px;letter-spacing:-0.5px;color:var(--red);transform:scaleY(1.15);transform-origin:top left;white-space:nowrap}
  .back-subtitle{margin-top:18px;text-align:center;font-family:"Roboto",sans-serif;font-style:italic;font-weight:300;font-size:14px;line-height:21px;color:var(--ink)}
  .back-subtitle b{font-family:"Oswald",sans-serif;font-style:normal;font-weight:500;font-size:13px}
  .back-body{margin-top:18px;font-family:"Arimo",sans-serif;font-size:12.6px;line-height:18.3px;color:var(--ink-soft);text-align:justify}
  .back-body p+p{margin-top:18px}

  /* Spine */
  .spine{position:absolute;left:535px;top:0;width:50px;height:792px}
  .spine-title{position:absolute;left:8px;top:42px;writing-mode:vertical-rl;font-family:"Oswald",sans-serif;font-weight:700;font-size:30px;line-height:34px;color:var(--red);letter-spacing:-0.3px}
  .spine-author{position:absolute;left:12px;top:590px;writing-mode:vertical-rl;font-family:"Roboto",sans-serif;font-weight:700;font-size:19px;letter-spacing:1px;color:var(--ink)}

  /* Front cover */
  .front-title{position:absolute;left:628px;top:40px;font-family:"Bebas Neue",sans-serif;font-size:118px;line-height:96px;letter-spacing:0.5px;white-space:nowrap}
  .front-title span{display:block}
  .runners-photo{position:absolute;left:772px;top:330px;width:320px;height:440px;background:radial-gradient(ellipse at 50% 40%,var(--photo-a) 0%,var(--photo-b) 70%,transparent 100%);border-radius:40% 40% 10% 10%}
  .tagline{position:absolute;left:612px;top:366px;width:180px;text-align:center;color:var(--ink)}
  .tagline-lead{font-family:"Oswald",sans-serif;font-weight:500;font-size:21px;line-height:26px;transform:scaleY(1.1)}
  .tagline-key{font-family:"Bebas Neue",sans-serif;font-size:58px;line-height:56px;color:#222}
  .tagline-rest{font-family:"Roboto",sans-serif;font-style:italic;font-weight:300;font-size:16.5px;line-height:22px}
  .front-author{position:absolute;left:630px;top:748px;font-family:"Roboto",sans-serif;font-weight:700;font-size:21px;letter-spacing:1px;color:#111}
</style>
</head>
<body>
<main class="spread">
  <section class="back">
    <h2 class="back-title">DISTANCE RACING BLUEPRINTS</h2>
    <p class="back-subtitle"><b>AN IN-DEPTH MANUAL</b> FOR ACHIEVING YOUR PEAK RACE DAY<br>FEATURING SCHEDULES, COUNSEL AND TARGET-REACHING POINTERS</p>
    <div class="back-body">
      <p>Lorem ipsum dolor sit amet, consectetur adipiscing elit, sed do eiusmod tempor incididunt ut labore et dolore magna aliqua. Quis ipsum suspendisse ultrices gravida. Risus commodo viverra maecenas accumsan lacus vel facilisis. Lorem ipsum dolor sit amet, consectetur adipiscing elit, sed do eiusmod tempor incididunt ut labore et dolore magna aliqua. Quis ipsum suspendisse ultrices gravida. Risus commodo viverra maecenas accumsan lacus vel facilisis. Lorem ipsum dolor sit amet, consectetur adipiscing elit, sed do eiusmod tempor incididunt ut labore et dolore magna aliqua. Quis ipsum suspendisse ultrices gravida. Risus commodo viverra maecenas accumsan lacus vel facilisis. Lorem ipsum dolor sit amet, consectetur adipiscing elit, sed do eiusmod tempor incididunt ut labore et dolore magna aliqua. Quis ipsum suspendisse ultrices gravida. Risus commodo viverra maecenas accumsan lacus vel facilisis.</p>
      <p>Lorem ipsum dolor sit amet, consectetur adipiscing elit, sed do eiusmod tempor incididunt ut labore et dolore magna aliqua. Quis ipsum suspendisse ultrices gravida. Risus commodo viverra maecenas accumsan lacus vel facilisis. Lorem ipsum dolor sit amet, consectetur adipiscing elit, sed do eiusmod tempor incididunt ut labore et dolore magna aliqua. Quis ipsum suspendisse ultrices gravida. Risus commodo viverra maecenas accumsan lacus vel facilisis. Lorem ipsum dolor sit amet, consectetur adipiscing elit, sed do eiusmod tempor incididunt ut labore et dolore magna aliqua. Quis ipsum suspendisse ultrices gravida. Risus commodo viverra maecenas accumsan lacus vel facilisis.</p>
    </div>
  </section>

  <section class="spine">
    <span class="spine-title">DISTANCE RACING BLUEPRINTS</span>
    <span class="spine-author">AUTHOR NAME</span>
  </section>

  <section class="front">
    <h1 class="front-title red-gradient"><span>DISTANCE</span><span>RACING</span><span>BLUEPRINTS</span></h1>
    <div class="runners-photo" role="img" aria-label="Photo of three smiling runners in athletic wear running toward the viewer"></div>
    <div class="tagline">
      <p class="tagline-lead">AN IN-DEPTH</p>
      <p class="tagline-key">MANUAL</p>
      <p class="tagline-rest">FOR ACHIEVING<br>YOUR PEAK<br>RACE DAY<br>FEATURING<br>SCHEDULES,<br>COUNSEL AND<br>TARGET-REACHING<br>POINTERS</p>
    </div>
    <p class="front-author">AUTHOR NAME</p>
  </section>
</main>
</body>
</html>
```